My name is Delia Okonkwo,I want to create a web page for my personal dog grooming business. The name on the web page can be "Delia's Dog Grooming" I am located in San Antonio Texas. The page would help grow my customer base. Before and after pictures would display the quality of work that I do. On my page I can provide information about myself, my services, and pricing.
Updates

I have updated project to guaranteed pay

Please try to incorporate a schnauzer in an icon or logo. My dog is a schnauzer. THANKS!!!!!!!!!!!!

Target Market(s)

Dog Owners

Industry/Entity Type

Business

Requirements
Must have
• -A spot for before and after pictures.
-An about me section
-A section to make an appointment
Nice to have
• My favorite Color is purple. I think different shades of purple would be nice or purple with a light green

please incorporate a schnauzer in any icon or logo. My dog is a schnauzer.

```html
<!DOCTYPE html>
<html lang="en">
<head>
<meta charset="utf-8">
<title>Delia's Dog Grooming</title>
<link href="https://fonts.googleapis.com/css2?family=Open+Sans:ital,wght@0,400;0,600;0,700;1,600&family=Arimo:wght@400;700&display=swap" rel="stylesheet">
<style>
:root{
  --plum-dark:#2c0f33;
  --plum:#4a1a55;
  --violet:#6b2a8c;
  --violet-light:#8c3fb0;
  --pink:#d84fb0;
  --lime:#b5e02a;
  --nav-text:#d9f26a;
  --grey-bg:#ebebeb;
  --body-text:#555;
  --lavender:#d8c8e2;
  --lavender-dark:#a890b3;
  --white:#fff;
}
*{margin:0;padding:0;box-sizing:border-box}
html,body{width:1200px;height:1037px;overflow:hidden}
body{position:relative;font-family:"Arimo",Arial,sans-serif;background:var(--grey-bg)}
.abs{position:absolute}

/* header */
.site-header{left:0;top:0;width:1200px;height:168px;background:radial-gradient(circle at 50% 40%,#4a1d50,var(--plum-dark))}
.brand{display:flex;align-items:center;gap:10px}
.brand-mark{width:40px;height:40px;border-radius:50%;background:var(--pink);flex:none}
.brand-name{font-family:"Open Sans",sans-serif;font-weight:600;color:var(--pink);line-height:1;white-space:nowrap}
.brand-name span{display:block}
.header-brand{left:150px;top:100px}
.header-brand .brand-name{font-size:25px}
.search{left:854px;top:96px;width:196px;height:23px;background:var(--white);border:1px solid #ccc;font-size:11px;color:#444;padding:4px 8px}
.search svg{position:absolute;right:6px;top:3px}
.main-nav{left:378px;top:129px;width:682px;height:33px;border:2px solid #b79ac0;background:linear-gradient(#5c2a68,#3a1544);display:flex;align-items:center;padding-left:23px;gap:13px;white-space:nowrap}
.main-nav a{color:var(--nav-text);text-decoration:none;font-size:12px;text-transform:uppercase;font-family:"Arimo",sans-serif;white-space:nowrap}

/* hero */
.hero-band{left:0;top:168px;width:1200px;height:330px;background:var(--lime)}
.hero{left:145px;top:180px;width:922px;height:303px;border-radius:22px;border:1px solid #c9a6de;background:linear-gradient(100deg,var(--violet-light) 0%,var(--violet) 55%,#4a1670 100%)}
.hero-photo{left:173px;top:198px;width:340px;height:267px;border:3px solid var(--white);border-radius:6px;background:linear-gradient(160deg,#6f7d68,#4c6b2f 60%,#6a8c3c)}
.hero-title{left:535px;top:246px;font-family:"Open Sans",sans-serif;font-style:italic;font-weight:600;font-size:33px;color:#e07ad0;white-space:nowrap}
.hero-sub{left:541px;top:290px;font-family:"Open Sans",sans-serif;font-weight:700;font-size:22px;color:var(--white)}
.hero-text{left:541px;top:332px;width:410px;font-size:11.5px;line-height:14px;color:var(--white)}
.btn{height:24px;border-radius:3px;font-family:"Open Sans",sans-serif;font-size:12px;display:flex;align-items:center;justify-content:center;border:1px solid #bbb;white-space:nowrap}
.btn-details{left:787px;top:440px;width:75px;background:linear-gradient(#fff,#ddd);color:#333}
.btn-appointment{left:876px;top:439px;width:75px;background:linear-gradient(#fff,#d9d0e6);color:var(--plum);font-size:9px;font-weight:600}
.dots{left:984px;top:456px;display:flex;gap:4px}
.dots span{width:12px;height:12px;border-radius:50%;background:var(--white)}
.dots span:first-child{background:#f08ad8}

/* about */
.about-heading{left:212px;top:507px;font-size:18px;font-weight:400;color:#2a1030}
.about-photo{left:156px;top:524px;width:199px;height:127px;border:2px solid var(--white);background:linear-gradient(90deg,#e8e2dc,#d9b27c 70%,#c9c0b5)}
.about-text{left:370px;top:508px;width:700px;font-size:10.2px;line-height:12.3px;color:var(--body-text)}
.about-text p{margin-bottom:12.3px}
.about-text p.tight{margin-bottom:0}

/* services */
.services{left:146px;top:662px;width:899px;height:242px;background:linear-gradient(var(--lavender),var(--lavender-dark));border:1px solid #ccc}
.services-bar{left:146px;top:662px;width:899px;height:35px;background:linear-gradient(#5a1c6e,#3a0f4a)}
.service-title{top:673px;font-family:"Open Sans",sans-serif;font-weight:600;font-size:12.5px;color:var(--white);text-transform:uppercase;white-space:nowrap}
.service-img{border:2px solid #9dd33a}
.img-appt{left:180px;top:703px;width:104px;height:114px;border:2px solid var(--plum);background:linear-gradient(#8c6aa8,#b9a6cc)}
.img-groom{left:384px;top:707px;width:173px;height:131px;background:linear-gradient(#6a6a6a,#2c2c2c)}
.img-gallery{left:583px;top:706px;width:201px;height:164px;background:linear-gradient(#8a7fa6,#2a2a2a)}
.img-before{left:803px;top:714px;width:224px;height:153px;background:linear-gradient(90deg,#b99268,#a87a4a 50%,#c2a37c)}
.know{font-size:11.5px;color:#222;white-space:nowrap}
.appt-text{left:156px;top:822px;width:205px;font-size:10.5px;line-height:13px;color:#555}

/* footer */
.site-footer{left:0;top:913px;width:1200px;height:124px;background:linear-gradient(#6e6670,#4a2d52 50%,#2a0c33)}
.footer-rule{left:152px;top:926px;width:892px;height:2px;background:#6a3c7a}
.footer-brand{left:162px;top:945px}
.footer-brand .brand-name{font-size:22px}
.footer-brand .brand-mark{width:36px;height:36px}
.copyright{left:415px;top:971px;font-size:11.5px;color:#c9b7cf;white-space:nowrap}
.footer-nav{left:181px;top:1003px;display:flex;gap:11px;white-space:nowrap}
.footer-nav a{color:var(--nav-text);font-size:10.5px;text-decoration:none}
.social{left:738px;top:940px;width:103px;height:62px;background:var(--white);border-radius:5px;display:grid;grid-template-columns:repeat(3,22px);gap:4px;padding:6px 14px;align-content:center}
.social span{width:22px;height:22px;border-radius:3px}
.payment-label{left:876px;top:936px;font-size:10.5px;color:#ddd}
.payment-list{left:876px;top:955px;display:flex;gap:7px;font-family:"Arimo",sans-serif;font-weight:700;font-size:10.5px;color:#8fb6e8;white-space:nowrap}
</style>
</head>
<body>

<header class="abs site-header">
  <div class="abs brand header-brand"><span class="brand-mark"></span><span class="brand-name"><span>Delia's</span><span>Dog Grooming</span></span></div>
  <div class="abs search">enter keyword(s)
    <svg width="15" height="15" viewBox="0 0 15 15"><circle cx="6" cy="6" r="4.5" fill="none" stroke="#aaa" stroke-width="1.5"/><line x1="9.5" y1="9.5" x2="14" y2="14" stroke="#aaa" stroke-width="2"/></svg>
  </div>
  <nav class="abs main-nav">
    <a href="#">Home</a><a href="#">About me</a><a href="#">Make an appointment</a><a href="#">Dog grooming</a><a href="#">Gallery</a><a href="#">Before &amp; after</a><a href="#">Contact us</a>
  </nav>
</header>

<section>
  <div class="abs hero-band"></div>
  <div class="abs hero"></div>
  <div class="abs hero-photo" role="img" aria-label="Photo of a miniature schnauzer standing on grass"></div>
  <h1 class="abs hero-title">Miniature Schnauzer</h1>
  <h2 class="abs hero-sub">ZWERGSCHNAUZER</h2>
  <p class="abs hero-text">The Miniature Schnauzer is one of three Schnauzer breeds that originated in Germany, the other two being the Standard and Giant. In their homeland they are known as the Zwergschnauzer, or Dwarf Schnauzer.</p>
  <a class="abs btn btn-details">DETAILS</a>
  <a class="abs btn btn-appointment">APPOINTMENT</a>
  <div class="abs dots"><span></span><span></span><span></span></div>
</section>

<section>
  <h2 class="abs about-heading">ABOUT ME</h2>
  <div class="abs about-photo" role="img" aria-label="Photo of the groomer with a golden dog"></div>
  <div class="abs about-text">
    <p class="tight">Grooming Salon is a "Young Makers Fund" and a "Best of Riverside" Award winning business and is situated in Oak Hollow; ideally placed to cater for Dogs and Cats from Riverside, Harbor Point and further afield throughout the Millbrook, North County and East County areas. Take a look around our site and get to know more about the animal grooming services we offer.</p>
    <p class="tight">We hope you like our site and look forward to welcoming you with your pet to our Fully Air Conditioned Grooming Salon.</p>
    <p class="tight">*Please note that there may be a waiting time for appointments. Although we have increased our staffing levels the delay could be up to 3 weeks during busy periods. Please allow for this and book/re-book early.</p>
    <p>Sometimes we have cancellation appointments available and operate a cancellation list, so please call or email for more details of our services and get information on the earliest appointment available.</p>
    <p>You are most welcome to wait for your Dog or Cat in our comfortable and spacious surroundings or drop your animal off and collect later.</p>
    <p>Microchipping is also available by appointment.</p>
  </div>
</section>

<section>
  <div class="abs services"></div>
  <div class="abs services-bar"></div>
  <h3 class="abs service-title" style="left:172px">Make an appointment</h3>
  <h3 class="abs service-title" style="left:408px">Dog grooming</h3>
  <h3 class="abs service-title" style="left:645px">Gallery</h3>
  <h3 class="abs service-title" style="left:855px">Before &amp; after</h3>

  <div class="abs img-appt" role="img" aria-label="Illustration of a groomed schnauzer with scissors"></div>
  <p class="abs appt-text">To arrange for a professional, friendly &amp; reliable service please get in touch via email at: hello@deliagroomingstudio.com or give us a call on: 01632 960418 or 07700 900315</p>

  <div class="abs service-img img-groom" role="img" aria-label="Photo of a schnauzer being groomed"></div>
  <span class="abs know" style="left:424px;top:851px">KNOW MORE...</span>

  <div class="abs service-img img-gallery" role="img" aria-label="Video still of a schnauzer on a grooming table"></div>
  <span class="abs know" style="left:640px;top:880px">KNOW MORE...</span>

  <div class="abs service-img img-before" role="img" aria-label="Before and after photos of a terrier on a grooming table"></div>
  <span class="abs know" style="left:877px;top:876px">KNOW MORE...</span>
</section>

<footer class="abs site-footer"></footer>
<div class="abs footer-rule"></div>
<div class="abs brand footer-brand"><span class="brand-mark"></span><span class="brand-name"><span>Delia's</span><span>Dog Grooming</span></span></div>
<p class="abs copyright">© 2012 deliagroomingstudio.com. All Rights Reserved.</p>
<nav class="abs footer-nav">
  <a href="#">Home</a><a href="#">About me</a><a href="#">Make an Appointment</a><a href="#">Dog Grooming</a><a href="#">Gallery</a><a href="#">Before &amp; After</a><a href="#">Contact Us</a>
</nav>
<div class="abs social">
  <span style="background:#f2a03a"></span><span style="background:#f5b43a"></span><span style="background:#4a6fb5"></span>
  <span style="background:#f0c040"></span><span style="background:#5ab3e8"></span><span style="background:#e8509a"></span>
</div>
<p class="abs payment-label">Payment accept</p>
<div class="abs payment-list"><span>Cardline</span><span>Duocard</span><span>Amerpay</span><span>PayNest</span></div>

</body>
</html>
```